Logo, Web and Mobile Designs for enterprise social media platform

All the details are in the attached document, please start reading the scope document first which explains what is this project about and the details about the needed deliverables, after that please read the UI_Requirements document which will detail what is expected regarding the coded web version since this is a coded contest, it is very important that you meet the UI requirements or suggest something else but we will need to agree first before working on the coded version

Good Luck

Target Market(s)

Enterprise Social Media

Industry/Entity Type

Media

Coding

Coded - Design and coding required

Number of Pages Required

5+ page

Font styles to use
Sans Serif

Requirements
Must have
• All the must haves are listed in the scope document so please check before you start

```html
<!DOCTYPE html>
<html lang="en">
<head>
<meta charset="utf-8">
<title>Teamorbit – Social Media Platform</title>
<link href="https://fonts.googleapis.com/css2?family=Open+Sans:wght@400;600;700&family=Raleway:wght@500;600;700;800&display=swap" rel="stylesheet">
<style>
:root{
  --blue:#1f6fd1;
  --blue-dark:#175fb8;
  --green:#4cc72a;
  --green-dark:#3aa91c;
  --ink:#333;
  --text:#666;
  --muted:#999;
  --line:#e3e3e3;
  --page:#eeeeee;
  --panel-head:#4a4a4a;
  --white:#fff;
}
*{box-sizing:border-box;margin:0;padding:0}
html,body{width:1200px;height:2211px;overflow:hidden}
body{background:var(--page);font-family:"Open Sans",Arial,sans-serif;color:var(--text);position:relative}
a{color:inherit;text-decoration:none}
.abs{position:absolute}

/* header */
.site-header{position:absolute;left:0;top:0;width:1200px;height:100px;background:var(--white)}
.brand{position:absolute;left:97px;top:33px;display:flex;align-items:center;gap:12px}
.brand-dot{width:36px;height:36px;border:4px solid var(--blue);border-radius:50%}
.brand-name{font-family:"Raleway",sans-serif;font-weight:800;font-size:23px;color:var(--blue);letter-spacing:.3px}
.search{position:absolute;left:323px;top:29px;width:352px;height:39px;border:1px solid #ccc;border-radius:3px;display:flex;align-items:center;justify-content:space-between;padding:0 14px;font-size:12px;color:var(--muted)}
.quick{position:absolute;top:14px;display:flex;flex-direction:column;align-items:center;width:76px;font-size:12px;line-height:14px;color:#555;text-align:center}
.quick-icon{width:38px;height:32px;border:1px solid #bbb;border-radius:4px;background:#f6f6f6;display:flex;align-items:center;justify-content:center;margin-bottom:3px}
.auth{position:absolute;top:34px;height:29px;border-radius:2px;color:#fff;font-size:12px;font-weight:600;display:flex;align-items:center;justify-content:center;gap:4px}
.auth.sign-in{left:955px;width:68px;background:var(--blue)}
.auth.sign-up{left:1032px;width:69px;background:var(--green)}

/* nav */
.main-nav{position:absolute;left:0;top:100px;width:1200px;height:46px;background:var(--blue)}
.main-nav a{position:absolute;top:0;line-height:46px;font-family:"Raleway",sans-serif;font-weight:700;font-size:13px;color:#fff}
.main-nav a.active{color:#7ef05a}
.main-nav a.plain{font-weight:500}

/* hero */
.hero{position:absolute;left:0;top:146px;width:1200px;height:416px;background:linear-gradient(115deg,#4a5260 0%,#8c8078 40%,#b3a196 55%,#58606c 80%,#3e4552 100%)}
.hero-title{position:absolute;left:0;width:1200px;text-align:center;color:#fff;font-family:"Raleway",sans-serif;text-shadow:0 2px 4px rgba(0,0,0,.35)}
.hero-title.small{top:126px;font-size:36px;font-weight:600;letter-spacing:1px}
.hero-title.big{top:170px;font-size:41px;font-weight:800}
.hero-btn{position:absolute;left:528px;top:236px;width:146px;height:43px;background:var(--green);border:1px solid #6fe04b;color:#fff;font-family:"Raleway",sans-serif;font-weight:700;font-size:13px;display:flex;align-items:center;justify-content:center}
.dots{position:absolute;top:355px;left:0;width:1200px;display:flex;justify-content:center;gap:5px}
.dots span{width:15px;height:15px;border:2px solid #fff;border-radius:50%}
.dots span.on{background:var(--green)}

/* panels */
.panel{position:absolute;background:#fff;border:1px solid #ddd}
.panel-head{height:44px;background:var(--panel-head);color:#fff;font-family:"Raleway",sans-serif;font-weight:700;font-size:16px;line-height:44px;padding-left:17px}
.component-list{list-style:none;padding:10px 0 0 0}
.component-list li{height:31px;line-height:31px;margin:0 0 0 16px;padding-left:8px;border-bottom:1px solid #eee;font-size:12px;color:#555}
.component-list li:last-child{border-bottom:0}

.recent{padding:0 0 0 15px}
.recent-item{display:flex;gap:16px;padding:13px 0 14px;border-bottom:1px solid #eee;margin-right:0}
.thumb{flex:none}
.recent-item .thumb{width:78px;height:70px;margin-top:2px}
.post-title{font-family:"Raleway",sans-serif;font-weight:700;font-size:12.5px;color:#333;text-decoration:underline;line-height:16px}
.meta{font-size:11px;color:var(--green-dark);line-height:18px;display:flex;align-items:center;gap:4px}
.meta .sep{color:#999;margin:0 4px}
.excerpt{font-size:12px;line-height:18px;color:#666}
.see-more{text-align:right;padding:14px 26px 0 0;font-size:12px;color:var(--green-dark)}

.newsletter h3{font-family:"Raleway",sans-serif;font-weight:700;font-size:16px;color:#333;margin:16px 0 0 21px}
.email{margin:16px 0 0 20px;width:331px;height:37px;background:#f1f1f1;border:1px solid #e2e2e2;font-size:12px;color:#aaa;padding:10px 15px}
.subscribe{margin:11px 0 0 21px;width:83px;height:32px;background:var(--green);color:#fff;font-size:11px;font-weight:700;display:flex;align-items:center;justify-content:center}

.chat{position:absolute;left:97px;top:2015px;width:375px;height:78px;background:linear-gradient(90deg,var(--blue) 0%,#3f8ae6 100%)}
.chat h4{position:absolute;left:20px;top:13px;color:#fff;font-family:"Raleway",sans-serif;font-weight:700;font-size:15px}
.chat p{position:absolute;left:20px;top:40px;color:#fff;font-size:12px}
.chat .agent{position:absolute;right:0;top:-10px;width:98px;height:98px;border-radius:50%;border:4px solid #fff;background:linear-gradient(160deg,#c79a80,#6a4a3c)}

/* cards */
.card{position:absolute;background:#fff;border:1px solid #ddd;padding:5px}
.card-title{font-family:"Raleway",sans-serif;font-weight:700;color:#333}
.actions{display:flex;gap:8px}
.btn{display:flex;align-items:center;gap:5px;background:#f0f0f0;border:1px solid #d6d6d6;border-radius:2px;color:#888}
.btn svg{fill:#999}
.read{color:var(--green-dark)}

.feature .thumb{width:580px;height:238px}
.feature .card-title{font-size:14.5px;margin:23px 0 0 10px}
.feature .excerpt{font-size:12px;line-height:22.5px;margin:10px 10px 0 10px}
.feature .actions{margin:18px 0 0 10px;gap:12px}
.feature .btn{height:32px;padding:0 12px;font-size:12px}

.tile{width:284px;height:318px}
.tile .thumb{width:272px;height:152px}
.tile .card-title{font-size:14px;margin:16px 0 0 4px}
.tile .excerpt{font-size:11.5px;line-height:23px;margin:8px 0 0 4px}
.tile .actions{margin:10px 0 0 4px;gap:4px}
.tile .btn{height:21px;padding:0 6px;font-size:8px;gap:3px}

.feed{left:509px;top:1722px;width:592px;height:371px;padding:0}
.feed-main{position:absolute;left:18px;top:20px;width:241px;height:330px;background:#f7f7f7;border:1px solid #e6e6e6}
.feed-main .thumb{width:239px;height:175px}
.feed-main .card-title{font-size:14.5px;margin:14px 0 0 11px}
.feed-main .meta{margin:2px 0 0 11px}
.feed-main .excerpt{font-size:11.5px;line-height:22px;margin:5px 0 0 11px}
.feed-main .actions{margin:10px 0 0 11px;gap:5px}
.feed-main .btn{height:20px;padding:0 6px;font-size:7.5px;gap:3px}
.feed-list{position:absolute;left:281px;top:22px}
.feed-item{display:flex;gap:18px;height:67px}
.feed-item .thumb{width:71px;height:56px}
.feed-item .post-title{font-size:12.5px;margin-top:2px}
.feed-item .meta{margin-top:6px}

/* footer */
.site-footer{position:absolute;left:0;top:2137px;width:1200px;height:74px;background:#fff;border-top:1px solid #ddd}
.site-footer .copy{position:absolute;left:97px;top:19px;font-size:12px;color:#666;line-height:22px}
.site-footer .copy span{margin:0 6px;color:#999}
.social{position:absolute;right:98px;top:25px;display:flex;gap:13px}
.social span{width:22px;height:22px;border-radius:3px}
</style>
</head>
<body>

<header class="site-header">
  <div class="brand"><span class="brand-dot"></span><span class="brand-name">TEAMORBIT</span></div>
  <div class="search"><span>SEARCH..</span>
    <svg width="14" height="14" viewBox="0 0 14 14"><circle cx="6" cy="6" r="4.5" fill="none" stroke="#888" stroke-width="1.6"/><line x1="9.3" y1="9.3" x2="13" y2="13" stroke="#888" stroke-width="1.8"/></svg>
  </div>
  <div class="quick" style="left:701px"><span class="quick-icon"><svg width="14" height="16" viewBox="0 0 14 16"><circle cx="7" cy="4.5" r="3.5" fill="#888"/><path d="M0 16c0-5 3-7 7-7s7 2 7 7z" fill="#888"/></svg></span>Add<br>Subscribe</div>
  <div class="quick" style="left:778px"><span class="quick-icon"><svg width="20" height="14" viewBox="0 0 20 14"><circle cx="6" cy="4" r="3" fill="#888"/><circle cx="14" cy="4" r="3" fill="#888"/><path d="M0 14c0-4 2.5-6 6-6s6 2 6 6zM8 14c0-4 2.5-6 6-6s6 2 6 6z" fill="#888"/></svg></span>Add<br>Participate</div>
  <div class="quick" style="left:855px"><span class="quick-icon"><svg width="13" height="16" viewBox="0 0 13 16"><path d="M1 1h8l3 3v11H1z" fill="none" stroke="#888" stroke-width="1.5"/><line x1="3.5" y1="8" x2="9.5" y2="8" stroke="#888"/><line x1="3.5" y1="11" x2="9.5" y2="11" stroke="#888"/></svg></span>Associate<br>Surveys</div>
  <a class="auth sign-in" href="#"><svg width="9" height="10" viewBox="0 0 9 10"><rect x="0" y="4" width="9" height="6" fill="#fff"/><path d="M2 4V3a2.5 2.5 0 0 1 5 0v1" fill="none" stroke="#fff" stroke-width="1.4"/></svg>Sign in</a>
  <a class="auth sign-up" href="#"><svg width="10" height="10" viewBox="0 0 10 10"><path d="M1 9l1-3 5-5 2 2-5 5z" fill="#fff"/></svg>Sign Up</a>
</header>

<nav class="main-nav">
  <a class="active" style="left:127px" href="#">HOME</a>
  <a style="left:213px" href="#">PROFILE</a>
  <a style="left:313px" href="#">RESOURCES</a>
  <a style="left:435px" href="#">NEWS</a>
  <a style="left:524px" href="#">EVENTS</a>
  <a style="left:622px" href="#">CONATCT US</a>
  <a class="plain" style="left:917px" href="#">Buisness Services</a>
  <a class="plain" style="left:1050px" href="#">Upgrade</a>
</nav>

<section class="hero" role="img" aria-label="Hand touching a tablet surrounded by floating social media icons">
  <div class="hero-title small">TEAMORBIT</div>
  <div class="hero-title big">SOCIAL MEDIA PLATFORM</div>
  <a class="hero-btn" href="#">READ MORE &gt;&gt;</a>
  <div class="dots"><span class="on"></span><span></span><span></span><span></span></div>
</section>

<!-- sidebar -->
<aside class="panel" style="left:97px;top:593px;width:375px;height:803px">
  <div class="panel-head">COMPONENTS</div>
  <ul class="component-list">
    <li>Container</li><li>Dividers</li><li>Menu</li><li>Toolbar</li><li>Tabs</li><li>Top Nav</li><li>Side Nav</li><li>Sliders</li><li>Progress Bars</li><li>Switch Buttons</li><li>Expandable and Collapsable List Controls</li><li>Cards</li><li>Dialogs</li><li>Tooltips</li><li>Steppers</li><li>Chips</li><li>Snackbar ( Toast )</li><li>Tables</li><li>Forms</li><li>Controls</li><li>Upload Files</li><li>Date Picker</li><li>Time Picker</li><li>Calendar</li>
  </ul>
</aside>

<aside class="panel" style="left:97px;top:1418px;width:375px;height:395px">
  <div class="panel-head">RECENT POST</div>
  <div class="recent">
    <div class="recent-item"><div class="thumb" role="img" aria-label="People at a gathering" style="background:linear-gradient(135deg,#b8322a,#e8d4c4,#6a4c3a)"></div>
      <div><div class="post-title">FINIBUS BONORUM ET MAL</div><div class="meta">▦ 18/11/2015 <span class="sep">|</span> ● Admin</div><div class="excerpt">At vero eos et accusamus et iusto odio dign<br>issimos ducimus qui blanditii..</div></div></div>
    <div class="recent-item"><div class="thumb" role="img" aria-label="Conference audience" style="background:linear-gradient(135deg,#6a5040,#c8a888,#3a3030)"></div>
      <div><div class="post-title">FINIBUS BONORUM ET MAL</div><div class="meta">▦ 18/11/2015 <span class="sep">|</span> ● Admin</div><div class="excerpt">At vero eos et accusamus et iusto odio dign<br>issimos ducimus qui blanditii..</div></div></div>
    <div class="recent-item" style="border-bottom:1px solid #eee"><div class="thumb" role="img" aria-label="Seminar hall" style="background:linear-gradient(135deg,#8a2a20,#d89070,#402020)"></div>
      <div><div class="post-title">FINIBUS BONORUM ET MAL</div><div class="meta">▦ 18/11/2015 <span class="sep">|</span> ● Admin</div><div class="excerpt">At vero eos et accusamus et iusto odio dign<br>issimos ducimus qui blanditii..</div></div></div>
  </div>
  <div class="see-more">See More &gt;&gt;</div>
</aside>

<aside class="panel newsletter" style="left:97px;top:1838px;width:375px;height:155px">
  <h3>NEWSLETTER SUBSCRIPTION</h3>
  <div class="email">Email address</div>
  <a class="subscribe" href="#">SUBSCRIBE</a>
</aside>

<aside class="chat">
  <h4>HAVE QUESTIONS ?</h4>
  <p>Let's Chat Now</p>
  <div class="agent" role="img" aria-label="Support agent with headset"></div>
</aside>

<!-- main column -->
<article class="card feature" style="left:509px;top:593px;width:592px;height:420px">
  <div class="thumb" role="img" aria-label="Speaker on stage addressing a conference audience" style="background:linear-gradient(180deg,#c9c2d4 0%,#8e8aa0 45%,#3a3438 100%)"></div>
  <div class="card-title">NEMO ENIM IPSAM VOLUPTATEM QUASPERNATUR AUT ODIT</div>
  <p class="excerpt">Sed ut perspiciatis unde omnis iste natus error sit voluptatem accusantium doloremque laudantiu totam rem aperiam, eaque ipsa quae ab illo inventore veritatis et quasi architecto beatae vitae dicta sunt explicabom voluptatem quia voluptas sit aspernatu.. <span class="read">Read More &gt;&gt;</span></p>
  <div class="actions">
    <span class="btn"><svg width="12" height="10" viewBox="0 0 12 10"><ellipse cx="6" cy="4.5" rx="6" ry="4.5"/></svg>Comments</span>
    <span class="btn"><svg width="11" height="10" viewBox="0 0 11 10"><rect x="0" y="4" width="3" height="6"/><path d="M4 4l3-4h1v3h3v7H4z"/></svg>Like</span>
    <span class="btn"><svg width="10" height="10" viewBox="0 0 10 10"><circle cx="2" cy="5" r="2"/><circle cx="8" cy="2" r="2"/><circle cx="8" cy="8" r="2"/><path d="M2 5L8 2M2 5l6 3" stroke="#999"/></svg>Share</span>
    <span class="btn"><svg width="10" height="10" viewBox="0 0 10 10"><path d="M5 1a4 4 0 1 0 4 4" fill="none" stroke="#999" stroke-width="1.6"/><path d="M4 0l3 1-2 2z"/></svg>Updates</span>
  </div>
</article>

<article class="card tile" style="left:509px;top:1035px">
  <div class="thumb" role="img" aria-label="Hands with a tablet and social icons on a table" style="background:linear-gradient(135deg,#c05a3a,#3aa8b8,#d89040)"></div>
  <div class="card-title">QUASPERNATUR AUT ODIT</div>
  <p class="excerpt">Veritatis et quasi architecto beatae vitae dic ta sunt explicabom voluptatem qutas sit aspernatu.. <span class="read">Read More &gt;&gt;</span></p>
  <div class="actions"><span class="btn"><svg width="8" height="7"><ellipse cx="4" cy="3.5" rx="4" ry="3"/></svg>Comments</span><span class="btn"><svg width="7" height="7"><rect width="7" height="7"/></svg>Like</span><span class="btn"><svg width="7" height="7"><circle cx="3.5" cy="3.5" r="3"/></svg>Share</span><span class="btn"><svg width="7" height="7"><circle cx="3.5" cy="3.5" r="3"/></svg>Updates</span></div>
</article>

<article class="card tile" style="left:817px;top:1035px">
  <div class="thumb" role="img" aria-label="Hand holding a tablet showing app icons" style="background:linear-gradient(135deg,#1a3a70,#6a9ad0,#2a6a98)"></div>
  <div class="card-title">QUASPERNATUR AUT ODIT</div>
  <p class="excerpt">Veritatis et quasi architecto beatae vitae dic ta sunt explicabom voluptatem qutas sit aspernatu.. <span class="read">Read More &gt;&gt;</span></p>
  <div class="actions"><span class="btn"><svg width="8" height="7"><ellipse cx="4" cy="3.5" rx="4" ry="3"/></svg>Comments</span><span class="btn"><svg width="7" height="7"><rect width="7" height="7"/></svg>Like</span><span class="btn"><svg width="7" height="7"><circle cx="3.5" cy="3.5" r="3"/></svg>Share</span><span class="btn"><svg width="7" height="7"><circle cx="3.5" cy="3.5" r="3"/></svg>Updates</span></div>
</article>

<article class="card tile" style="left:509px;top:1377px">
  <div class="thumb" role="img" aria-label="Presenter in front of a projected chart" style="background:linear-gradient(180deg,#9aa8b8 0%,#8a5a30 50%,#3a2418 100%)"></div>
  <div class="card-title">QUASPERNATUR AUT ODIT</div>
  <p class="excerpt">Veritatis et quasi architecto beatae vitae dic ta sunt explicabom voluptatem qutas sit aspernatu.. <span class="read">Read More &gt;&gt;</span></p>
  <div class="actions"><span class="btn"><svg width="8" height="7"><ellipse cx="4" cy="3.5" rx="4" ry="3"/></svg>Comments</span><span class="btn"><svg width="7" height="7"><rect width="7" height="7"/></svg>Like</span><span class="btn"><svg width="7" height="7"><circle cx="3.5" cy="3.5" r="3"/></svg>Share</span><span class="btn"><svg width="7" height="7"><circle cx="3.5" cy="3.5" r="3"/></svg>Updates</span></div>
</article>

<article class="card tile" style="left:817px;top:1377px">
  <div class="thumb" role="img" aria-label="Training session in a bright classroom" style="background:linear-gradient(180deg,#e6e2dc 0%,#a07050 60%,#5a3424 100%)"></div>
  <div class="card-title">QUASPERNATUR AUT ODIT</div>
  <p class="excerpt">Veritatis et quasi architecto beatae vitae dic ta sunt explicabom voluptatem qutas sit aspernatu.. <span class="read">Read More &gt;&gt;</span></p>
  <div class="actions"><span class="btn"><svg width="8" height="7"><ellipse cx="4" cy="3.5" rx="4" ry="3"/></svg>Comments</span><span class="btn"><svg width="7" height="7"><rect width="7" height="7"/></svg>Like</span><span class="btn"><svg width="7" height="7"><circle cx="3.5" cy="3.5" r="3"/></svg>Share</span><span class="btn"><svg width="7" height="7"><circle cx="3.5" cy="3.5" r="3"/></svg>Updates</span></div>
</article>

<section class="card feed">
  <div class="feed-main">
    <div class="thumb" role="img" aria-label="Group of people viewed from above with balloons" style="background:linear-gradient(135deg,#c8d0d8,#6a90b8,#d0c8c0)"></div>
    <div class="card-title">VOLUPTATEM QUASPERN</div>
    <div class="meta">▦ 18/11/2015 <span class="sep">|</span> ● Admin</div>
    <p class="excerpt">Sed ut perspiciatis unde omnis iste nv entore veritatis .. <span class="read">Read More &gt;&gt;</span></p>
    <div class="actions"><span class="btn"><svg width="7" height="6"><ellipse cx="3.5" cy="3" rx="3.5" ry="3"/></svg>Comments</span><span class="btn"><svg width="6" height="6"><rect width="6" height="6"/></svg>Like</span><span class="btn"><svg width="6" height="6"><circle cx="3" cy="3" r="3"/></svg>Share</span><span class="btn"><svg width="6" height="6"><circle cx="3" cy="3" r="3"/></svg>Updates</span></div>
  </div>
  <div class="feed-list">
    <div class="feed-item"><div class="thumb" role="img" aria-label="Network of connected people" style="background:linear-gradient(135deg,#1a2a48,#6a88b0)"></div><div><div class="post-title">DIGNISSIMOS DUCDFE LANDITIIS</div><div class="meta">▦ 18/11/2015 <span class="sep">|</span> ● Admin</div></div></div>
    <div class="feed-item"><div class="thumb" role="img" aria-label="Business team" style="background:linear-gradient(135deg,#d8d8d8,#3a4050)"></div><div><div class="post-title">DIGNISSIMOS DUCDFE LANDITIIS</div><div class="meta">▦ 18/11/2015 <span class="sep">|</span> ● Admin</div></div></div>
    <div class="feed-item"><div class="thumb" role="img" aria-label="Glowing digital network" style="background:linear-gradient(135deg,#2a2050,#7a60c0)"></div><div><div class="post-title">DIGNISSIMOS DUCDFE LANDITIIS</div><div class="meta">▦ 18/11/2015 <span class="sep">|</span> ● Admin</div></div></div>
    <div class="feed-item"><div class="thumb" role="img" aria-label="Smartphone with apps" style="background:linear-gradient(135deg,#e0dcd8,#a04050)"></div><div><div class="post-title">DIGNISSIMOS DUCDFE LANDITIIS</div><div class="meta">▦ 18/11/2015 <span class="sep">|</span> ● Admin</div></div></div>
    <div class="feed-item"><div class="thumb" role="img" aria-label="Businessman with social icons" style="background:linear-gradient(135deg,#8ab0d8,#c09060)"></div><div><div class="post-title">DIGNISSIMOS DUCDFE LANDITIIS</div><div class="meta">▦ 18/11/2015 <span class="sep">|</span> ● Admin</div></div></div>
  </div>
</section>

<footer class="site-footer">
  <div class="copy">Copyrights © 2015 Teamorbit. All Rights Reserved.<br>Terms &amp; Conditions<span>|</span>Privacy Policy<span>|</span>Sitemap</div>
  <div class="social" aria-label="Social links">
    <span style="background:#2d4f8f"></span><span style="background:#2aa3e0"></span><span style="background:#d2452f"></span><span style="background:#c8232c"></span><span style="background:#f07c1a"></span><span style="background:#333"></span>
  </div>
</footer>

</body>
</html>
```